Business card design needed

Family General Practitioner/ Family Physician.
Logo is the logo of the Noble Guild of Family Healers Oceania
http://kpltw.varendo.example/ImageShelf/marks/pages/NGFHO%20mark_jpg.htm
Updates

Project Deadline Extended
Reason: Just a bit more time to make changes and the weekend for me to look at things closely and to choose. Thanks, Orin

Thanks for all the submissions. So many of them are really works of art. Not one of them are not good. The ones that I am eliminating are the ones that I think are not suitable for me personally only, and because if I don't, it makes it very difficult to decide as many of you are also sending me slight variations of a card. I have just decided to choose a second place card too. Can't thank you all enough. Good luck, Orin. P.S - Working today till 10 pm as the card says :-), so probably won't be able to give a feedback till late Saturday night or Sunday morning here in Sydney, Australia. 

Project Deadline Extended
Reason: Just added a second place to the budget and realised that Australia is ahead of the rest of the world in the time zone (only :-) - don't want to offend anyone or start a debate!! ) , so Monday deadline will mean it will be a weekend for the rest of the world. Just wanted to give everyone more time to submit their best, especially since I will be picking a second card too. Can't thank everyone enough for the submissions. P.S - Not keen on photos on the card.

Industry/Entity Type

Business

Contact Information for Business Card

Dr. Orin Halvey M.B.B.S., F.N.G.F.H.O
Family General Practitioner
Address, timings, phone and fax number on the back.

Requirements
Must have
• Timings
Mon 7 am - 7 pm
Tues 7 am - 12 pm
Wed 7 am - 10 pm
Thurs 7 am - 12 pm
Fri 7 am - 8 pm
Sat 8 am - 10 pm
Sun - Off

```html
<!DOCTYPE html>
<html lang="en">
<head>
<meta charset="utf-8">
<title>Dr. Orin Halvey – Business Card</title>
<link rel="stylesheet" href="https://fonts.googleapis.com/css2?family=Roboto+Condensed:wght@400;700&display=swap">
<style>
  :root {
    --page-bg: #cfcbc1;
    --card-navy: #233757;
    --band-blue: #213f66;
    --ink-tan: #a39a82;
    --ink-tan-light: #b3ab95;
  }
  * { box-sizing: border-box; margin: 0; padding: 0; }
  html, body { width: 1200px; height: 960px; overflow: hidden; }
  body {
    background: var(--page-bg);
    font-family: "Roboto Condensed", "Arial Narrow", sans-serif;
    color: var(--ink-tan);
    display: flex;
    align-items: center;
    justify-content: center;
    gap: 60px;
  }
  .card {
    width: 520px;
    height: 300px;
    background: var(--card-navy);
    position: relative;
    overflow: hidden;
    box-shadow: 0 6px 18px rgba(0,0,0,.25);
  }
  /* Front */
  .card-front .name {
    position: absolute; top: 58px; width: 100%;
    text-align: center;
    font-weight: 700; font-size: 40px; letter-spacing: -0.5px;
    color: var(--ink-tan-light);
  }
  .card-front .credentials {
    position: absolute; top: 112px; width: 100%;
    text-align: center;
    font-size: 21px; letter-spacing: 1px;
  }
  .card-front .title-band {
    position: absolute; top: 188px; left: 0; right: 0; height: 46px;
    background: var(--band-blue);
    display: flex; align-items: center; justify-content: center;
    font-size: 24px;
  }
  /* Back */
  .hours {
    position: absolute; top: 16px; left: 70px;
    width: 380px;
    border-collapse: collapse;
    white-space: nowrap;
  }
  .hours td { padding: 0; height: 29px; line-height: 29px; }
  .hours .day { font-size: 18px; text-align: left; }
  .hours .time { font-size: 20px; text-align: right; color: var(--ink-tan-light); }
  .address-band {
    position: absolute; top: 230px; left: 0; right: 0; height: 28px;
    background: var(--band-blue);
    display: flex; align-items: center; justify-content: center;
    font-size: 15px; white-space: nowrap;
  }
  .phone {
    position: absolute; top: 266px; width: 100%;
    text-align: center; font-size: 15px; white-space: nowrap;
  }
</style>
</head>
<body>
  <section class="card card-front" aria-label="Card front">
    <h1 class="name">Dr. Orin Halvey</h1>
    <p class="credentials">M.B.B.S.,&nbsp; F.N.G.F.H.O.</p>
    <p class="title-band">Family General Practitioner</p>
  </section>

  <section class="card card-back" aria-label="Card back">
    <table class="hours">
      <tr><td class="day">Monday</td><td class="time">7 AM - 7 PM</td></tr>
      <tr><td class="day">Tuesday</td><td class="time">7 AM - 12 PM</td></tr>
      <tr><td class="day">Wednesday</td><td class="time">7 AM - 10 PM</td></tr>
      <tr><td class="day">Thursday</td><td class="time">7 AM - 12 PM</td></tr>
      <tr><td class="day">Friday</td><td class="time">7 AM - 8 PM</td></tr>
      <tr><td class="day">Saturday</td><td class="time">8 AM - 10 PM</td></tr>
      <tr><td class="day">Sunday</td><td class="time">OFF</td></tr>
    </table>
    <p class="address-band">Upper Level, Arcade Court, Hillcrest Towers Shopping Centre</p>
    <p class="phone">Ph 02 5550 0154 &nbsp;·&nbsp; Fax 02 5550 0155</p>
  </section>
</body>
</html>
```